Tidal Forge - Crypto Currency Miner Powered by Renewable Energy Website

We Need Web Pages Design for Website for Crypto Currency Miner

Serivices include:
Mining Rig Sales
Housing for Rigs turnkey on renewable energy grid
Cloud Mining term packages
Updates

http://www.vaultrigsurvey.example (Competitors sites)

Target Market(s)

Investers for Mining Rigs and terms for 1,2 or 3 years of Hash rate

Industry/Entity Type

Mining

Number of Pages Required

5+ page

Font styles to use
Sans Serif

Colors
add136
9bcb3c
606060
474747
ffc214
cadf82
fbee3e
876aae
6b449b

Requirements
Must have
• Pictures of Solar, Wind and power Factor Correction units
Nice to have
• e-commerce platform so contract terms can be purchased through website
Should not have
• Heavy construction equipment

```html
<!DOCTYPE html>
<html lang="en">
<head>
<meta charset="utf-8">
<title>Tidal Forge – Renewable Crypto Mining</title>
<link href="https://fonts.googleapis.com/css2?family=Nunito:wght@400;600;700;800&family=Lato:wght@400;700&display=swap" rel="stylesheet">
<style>
:root{
  --green:#9bcb3c;
  --yellow:#ffc214;
  --pale-yellow:#fbee3e;
  --soft-green:#cadf82;
  --purple:#6b449b;
  --lilac:#876aae;
  --ink:#1c1c22;
  --grey:#606060;
  --dark-grey:#474747;
  --panel:#f6f6f8;
  --footer:#2c2123;
  --footer-bar:#1f1517;
  --white:#ffffff;
}
*{box-sizing:border-box;margin:0;padding:0}
html,body{width:1200px;height:2853px;overflow:hidden}
body{position:relative;background:var(--white);font-family:"Lato",sans-serif;color:var(--grey)}
.abs{position:absolute}
.heading{font-family:"Nunito",sans-serif;font-weight:800}

/* hero */
.hero{left:0;top:0;width:1200px;height:600px;background:linear-gradient(180deg,#5a5466 0%,#4a4d68 45%,#3d4a72 100%)}
.hero-wave{left:0;top:520px;width:1200px;height:90px}
.brand{display:flex;align-items:center;gap:10px;font-family:"Nunito",sans-serif;font-weight:800;color:var(--white);font-size:24px}
.brand-dot{width:30px;height:30px;border-radius:50%;background:var(--green)}
.nav{top:57px;left:390px;font-family:"Nunito",sans-serif;font-weight:700;font-size:11.5px;color:var(--white);text-transform:uppercase}
.nav a{color:inherit;text-decoration:none;position:absolute;white-space:nowrap}
.nav a.active{color:var(--green)}
.phone{left:925px;top:48px;display:flex;align-items:center;gap:10px;color:var(--white);font-family:"Nunito",sans-serif;font-weight:700;font-size:13px;white-space:nowrap}
.hero-title{left:0;width:1200px;top:302px;text-align:center;color:var(--white);font-size:50px;letter-spacing:.5px}
.hero-sub{left:0;width:1200px;top:364px;text-align:center;color:var(--white);font-family:"Nunito",sans-serif;font-weight:600;font-size:24px}
.btn{display:flex;align-items:center;justify-content:center;font-family:"Nunito",sans-serif;font-weight:800;font-size:12px;color:var(--white);text-transform:uppercase;border-radius:22px 22px 22px 0}
.btn-hero{left:512px;top:422px;width:175px;height:46px;background:var(--yellow)}

/* dots decoration */
.dots{width:88px;height:50px}

/* about */
.about-photo{left:0;top:713px;width:571px;height:424px;border-radius:0 110px 110px 0;background:linear-gradient(135deg,#6d8fc0 0%,#2a4a7a 45%,#f4c56a 70%,#8a7a60 100%);box-shadow:0 14px 30px rgba(0,0,0,.18)}
.about-title{left:648px;top:835px;font-size:46px;color:var(--purple)}
.about-text{left:648px;top:906px;width:400px;font-size:12px;line-height:17px;color:var(--grey)}
.about-text p+p{margin-top:14px}
.btn-about{left:648px;top:1067px;width:176px;height:46px;background:var(--purple)}

/* terms */
.terms{left:0;top:1246px;width:1200px;height:480px;background:var(--panel)}
.terms-wave{left:0;top:1230px;width:1200px;height:40px}
.section-title{left:0;width:1200px;text-align:center;font-size:37px;color:var(--ink)}
.term{width:300px;text-align:center}
.term-num{font-family:"Nunito",sans-serif;font-weight:700;font-size:46px;line-height:46px}
.term-num span{font-size:16px;color:var(--ink);margin-left:4px}
.term-label{font-family:"Nunito",sans-serif;font-weight:700;font-size:13px;margin-top:4px}
.term-text{font-size:11.5px;line-height:17px;margin-top:12px;color:var(--grey);padding:0 33px}

/* services */
.card{top:1978px;width:272px;height:293px;border-radius:12px;overflow:hidden;box-shadow:0 6px 16px rgba(0,0,0,.12)}
.card-yellow{background:linear-gradient(160deg,#ffd23a 0%,#ffc214 60%,#f3b50c 100%)}
.card-photo{position:absolute;left:0;top:0;width:272px;height:196px}
.card-foot{position:absolute;left:0;top:196px;width:272px;height:97px;background:var(--purple);display:flex;align-items:center;gap:14px;padding-left:24px}
.card-icon{width:54px;height:54px;border-radius:50%;border:2px solid var(--white);display:flex;align-items:center;justify-content:center;flex:none}
.card-name{font-family:"Nunito",sans-serif;font-weight:700;font-size:17px;line-height:21px;color:var(--white)}

/* footer */
.footer{left:0;top:2380px;width:1200px;height:406px;background:linear-gradient(180deg,#3a2e31 0%,var(--footer) 100%)}
.footer-wave{left:0;top:2352px;width:1200px;height:60px}
.footer-brand{left:0;width:1200px;top:2462px;justify-content:center}
.news-title{left:0;width:1200px;top:2542px;text-align:center;font-size:36px;color:var(--white)}
.email{left:361px;top:2632px;width:476px;height:32px;border-bottom:1px solid rgba(255,255,255,.7);display:flex;align-items:center;justify-content:space-between;color:var(--white);font-family:"Nunito",sans-serif;font-weight:700;font-size:11.5px;padding:0 6px}
.footer-text{left:330px;width:540px;top:2710px;text-align:center;color:var(--white);font-size:11.5px;line-height:21px}
.bottom-bar{left:0;top:2786px;width:1200px;height:67px;background:var(--footer-bar);color:var(--white);font-size:11.5px}
.bottom-bar .copy{position:absolute;left:160px;top:26px}
.bottom-bar .links{position:absolute;right:150px;top:26px}
</style>
</head>
<body>

<!-- Hero -->
<div class="abs hero" role="img" aria-label="Wind turbines against a dusk sky"></div>
<svg class="abs hero-wave" viewBox="0 0 1200 90" preserveAspectRatio="none"><path d="M0 40 C250 80 520 85 760 62 C950 44 1080 30 1200 40 L1200 90 L0 90Z" fill="#fff"/></svg>

<div class="abs brand" style="left:170px;top:45px"><span class="brand-dot"></span>Tidal Forge</div>
<nav class="abs nav">
  <a class="active" style="left:0">Home</a>
  <a style="left:68px">About Us</a>
  <a style="left:158px">Services</a>
  <a style="left:245px">Contract Terms</a>
  <a style="left:380px">FAQ</a>
  <a style="left:439px">Contact</a>
</nav>
<div class="abs phone">
  <svg width="16" height="28" viewBox="0 0 16 28"><rect x="1" y="1" width="14" height="26" rx="2.5" fill="none" stroke="#fff" stroke-width="1.6"/><line x1="6" y1="23" x2="10" y2="23" stroke="#fff" stroke-width="1.6"/></svg>
  +000 555 0142
</div>

<h1 class="abs heading hero-title">START BITCOIN MINING TODAY!</h1>
<p class="abs hero-sub">Join over 1.000.000 people with the world's leading hashpower provider</p>
<a class="abs btn btn-hero">Learn More</a>

<!-- About -->
<div class="abs about-photo" role="img" aria-label="Solar panels under a bright sun"></div>
<svg class="abs dots" style="left:650px;top:751px" viewBox="0 0 88 50"><circle cx="25" cy="25" r="24" fill="#fbee3e" opacity=".55"/><circle cx="44" cy="25" r="24" fill="#ffe86a" opacity=".55"/><circle cx="63" cy="25" r="24" fill="#fbee3e" opacity=".55"/></svg>
<h2 class="abs heading about-title">About Us</h2>
<div class="abs about-text">
  <p>Lorem ipsum dolor sit amet, consectetur adipiscing elit, sed do eiusmod tempor incididunt ut labore et dolore magna aliqua. Ut enim ad minim veniam,</p>
  <p>quis nostrud exercitation ullamco laboris nisi ut aliquip ex ea commodo consequat. Duis aute irure dolor in reprehenderit in voluptate velit esse cillum dolore eu fugiat nulla pariatur. Excepteur sint occaecat cupidatat non proident.</p>
</div>
<a class="abs btn btn-about">Learn More</a>

<!-- Terms -->
<div class="abs terms"></div>
<svg class="abs terms-wave" viewBox="0 0 1200 40" preserveAspectRatio="none"><path d="M0 18 C300 2 600 0 820 14 C1000 26 1100 24 1200 16 L1200 40 L0 40Z" fill="#f6f6f8"/></svg>
<svg class="abs dots" style="left:556px;top:1331px" viewBox="0 0 88 50"><circle cx="25" cy="25" r="24" fill="#fbee3e" opacity=".55"/><circle cx="44" cy="25" r="24" fill="#ffe86a" opacity=".55"/><circle cx="63" cy="25" r="24" fill="#fbee3e" opacity=".55"/></svg>
<h2 class="abs heading section-title" style="top:1408px">Mining Rigs Investors &amp; Terms For Hash Rate</h2>

<div class="abs term" style="left:143px;top:1500px">
  <div class="term-num" style="color:var(--yellow)">1<span>Year</span></div>
  <div class="term-label" style="color:var(--yellow)">1 years of Hash rate</div>
  <p class="term-text">Lorem ipsum dolor sit amet, consectetur adipiscing elit, sed do eiusmod tempor incididunt ut labore et dolore magna</p>
</div>
<div class="abs term" style="left:447px;top:1500px">
  <div class="term-num" style="color:var(--soft-green)">2<span>Year</span></div>
  <div class="term-label" style="color:var(--soft-green)">2 years of Hash rate</div>
  <p class="term-text">Lorem ipsum dolor sit amet, consectetur adipiscing elit, sed do eiusmod tempor incididunt ut labore et dolore magna</p>
</div>
<div class="abs term" style="left:731px;top:1500px">
  <div class="term-num" style="color:var(--purple)">3<span>Year</span></div>
  <div class="term-label" style="color:var(--purple)">3 years of Hash rate</div>
  <p class="term-text">Lorem ipsum dolor sit amet, consectetur adipiscing elit, sed do eiusmod tempor incididunt ut labore et dolore magna</p>
</div>

<!-- Services -->
<svg class="abs dots" style="left:556px;top:1816px" viewBox="0 0 88 50"><circle cx="25" cy="25" r="24" fill="#fbee3e" opacity=".55"/><circle cx="44" cy="25" r="24" fill="#ffe86a" opacity=".55"/><circle cx="63" cy="25" r="24" fill="#fbee3e" opacity=".55"/></svg>
<h2 class="abs heading section-title" style="top:1890px">Our Services</h2>

<div class="abs card card-yellow" style="left:160px" role="img" aria-label="Wind turbines and solar panels under a yellow tint">
  <svg width="272" height="293" viewBox="0 0 272 293"><line x1="136" y1="112" x2="136" y2="182" stroke="#fff" stroke-width="2"/><line x1="80" y1="147" x2="192" y2="147" stroke="#fff" stroke-width="2"/></svg>
</div>
<div class="abs card" style="left:464px">
  <div class="card-photo" role="img" aria-label="Rig site with equipment under a blue sky" style="background:linear-gradient(180deg,#5fa6e0 0%,#9cc7ea 45%,#e0733a 70%,#8b8b8b 100%)"></div>
  <div class="card-foot">
    <div class="card-icon"><svg width="28" height="22" viewBox="0 0 28 22"><path d="M7 19 H22 a5 5 0 0 0 0-10 a7 7 0 0 0-13-2 a6 6 0 0 0-2 12Z" fill="none" stroke="#fff" stroke-width="1.8"/></svg></div>
    <div class="card-name">Cloud Mining<br>term packages</div>
  </div>
</div>
<div class="abs card" style="left:768px">
  <div class="card-photo" role="img" aria-label="Energy pump silhouette at sunset" style="background:linear-gradient(180deg,#c9561a 0%,#f0a030 50%,#ffd36a 70%,#7a3a12 100%)"></div>
  <div class="card-foot">
    <div class="card-icon"><svg width="22" height="28" viewBox="0 0 22 28"><path d="M11 2 L11 26 M4 26 H18 M6 10 H16 M8 10 L4 26 M14 10 L18 26 M11 2 L6 8 H16Z" fill="none" stroke="#fff" stroke-width="1.8"/></svg></div>
    <div class="card-name">Housing for Rigs<br>turnkey on rene<br>wable energy grid</div>
  </div>
</div>

<!-- Footer -->
<div class="abs footer" role="img" aria-label="Wind turbines at night"></div>
<svg class="abs footer-wave" viewBox="0 0 1200 60" preserveAspectRatio="none"><path d="M0 12 C260 40 560 48 820 34 C1000 24 1110 14 1200 10 L1200 60 L0 60Z" fill="#3a2e31"/></svg>
<div class="abs brand footer-brand"><span class="brand-dot"></span>Tidal Forge</div>
<h2 class="abs heading news-title">Subscribe Our Newsletter Here</h2>
<div class="abs email">Enter Your Email
  <svg width="22" height="18" viewBox="0 0 22 18"><path d="M1 8 L21 1 L15 17 L10 10Z M10 10 L21 1" fill="#fff"/></svg>
</div>
<p class="abs footer-text">Lorem ipsum dolor sit amet, consectetur adipiscing elit, sed do eiusmod tempor incididunt ut labore et dolore magna aliqua. Ut enim ad minim veniam.</p>
<div class="abs bottom-bar">
  <span class="copy">Copyright © The Tidal Forge 2018. All Rights Reserved.</span>
  <span class="links">Privacy Policy &nbsp; / &nbsp; Terms and Condition</span>
</div>

</body>
</html>
```